Lawn care business card

I am looking for a quality designed personal business card to represent the quality and elegant nature of our company. We separate ourselves in our market by the aesthetic value of our work, so I am looking for marketing material that does the same. We target our marketing high end customers, and we try to avoid price shoppers. I am open to all design options, so long as they are in line with our companies values.

We are tend to go with a retro look on everything from our logo and print material, to our uniforms. We like to portray and "old fashion" set of core values, with a modern elegance. So a wild and crazy look is out of the question.

Things I'd like on the card:
1.) Logo
2.) Phone number: (816) 555-2931
3.) Website: Verdelynkc.com
4.) Email: robertfairley@verdelynkc.com
5.) My name: Robert Fairley
6.) Facebook link: friendpage.net/VerdelynGardenandGrounds
7.) Instagram: http://photoreel.net/verdelynkc

Attached is a copy of our logo.

Reason: More time is needed to gather conclusive feedback from the members of our marketing team.

```html
<!DOCTYPE html>
<html lang="en">
<head>
<meta charset="utf-8">
<title>Verdelyn Business Card</title>
<link href="https://fonts.googleapis.com/css2?family=Arimo:wght@400&display=swap" rel="stylesheet">
<style>
  :root {
    --page-bg: #efefef;
    --card-white: #ffffff;
    --card-dark: #252525;
    --text-light: #ececec;
    --text-muted: #d6d6d6;
    --brand-ink: #1f1f1f;
    --brand-accent: #e2582a;
    --icon-bg: #e4e4e4;
    --icon-ink: #2a2a2a;
  }
  html, body {
    margin: 0;
    padding: 0;
    width: 1200px;
    height: 864px;
    overflow: hidden;
    background: var(--page-bg);
    font-family: "Arimo", Helvetica, Arial, sans-serif;
  }
  .card {
    position: absolute;
    left: 100px;
    top: 146px;
    width: 1000px;
    height: 572px;
    display: flex;
    box-shadow: 0 10px 30px rgba(0,0,0,0.18);
  }
  .brand-panel {
    width: 430px;
    background: var(--card-white);
    display: flex;
    align-items: center;
    justify-content: center;
  }
  .brand {
    display: flex;
    align-items: center;
    gap: 16px;
  }
  .brand-dot {
    width: 30px;
    height: 30px;
    border-radius: 50%;
    background: var(--brand-accent);
  }
  .brand-name {
    font-size: 50px;
    color: var(--brand-ink);
    letter-spacing: 1px;
  }
  .info-panel {
    flex: 1;
    background: var(--card-dark);
    position: relative;
    color: var(--text-light);
  }
  .holder-name {
    position: absolute;
    right: 58px;
    top: 62px;
    margin: 0;
    font-size: 44px;
    font-weight: 400;
    letter-spacing: 0.5px;
  }
  .contact-list {
    list-style: none;
    margin: 0;
    padding: 0;
    position: absolute;
    right: 44px;
    top: 210px;
  }
  .contact-item {
    display: flex;
    justify-content: flex-end;
    align-items: center;
    height: 52px;
    font-size: 21px;
    color: var(--text-muted);
    white-space: nowrap;
  }
  .contact-icon {
    width: 26px;
    height: 26px;
    margin-left: 22px;
    background: var(--icon-bg);
    border-radius: 2px;
    display: flex;
    align-items: center;
    justify-content: center;
    flex: none;
  }
  .contact-icon svg { width: 18px; height: 18px; }
</style>
</head>
<body>
  <div class="card">
    <section class="brand-panel">
      <div class="brand">
        <span class="brand-dot"></span>
        <span class="brand-name">Verdelyn</span>
      </div>
    </section>
    <section class="info-panel">
      <h1 class="holder-name">Robert Fairley</h1>
      <ul class="contact-list">
        <li class="contact-item">(816) 555-2931
          <span class="contact-icon">
            <svg viewBox="0 0 24 24"><path fill="var(--icon-ink)" d="M6.6 10.8a15 15 0 0 0 6.6 6.6l2.2-2.2a1 1 0 0 1 1-.25 11.4 11.4 0 0 0 3.6.57 1 1 0 0 1 1 1V20a1 1 0 0 1-1 1A17 17 0 0 1 3 4a1 1 0 0 1 1-1h3.5a1 1 0 0 1 1 1c0 1.25.2 2.45.57 3.57a1 1 0 0 1-.25 1z"/></svg>
          </span>
        </li>
        <li class="contact-item">Verdelynkc.com
          <span class="contact-icon">
            <svg viewBox="0 0 24 24" fill="none" stroke="var(--icon-ink)" stroke-width="2"><circle cx="12" cy="12" r="9"/><path d="M3 12h18M12 3c3 3 3 15 0 18M12 3c-3 3-3 15 0 18"/></svg>
          </span>
        </li>
        <li class="contact-item">robertfairley@verdelynkc.com
          <span class="contact-icon">
            <svg viewBox="0 0 24 24" fill="none" stroke="var(--icon-ink)" stroke-width="2"><rect x="3" y="6" width="18" height="12"/><path d="M3 6l9 7 9-7"/></svg>
          </span>
        </li>
        <li class="contact-item">http://photoreel.net/verdelynkc
          <span class="contact-icon"></span>
        </li>
        <li class="contact-item">friendpage.net/VerdelynGardenandGrounds
          <span class="contact-icon"></span>
        </li>
      </ul>
    </section>
  </div>
</body>
</html>
```